Quarrybend Marble & Tile Needs a Business Card

Attached you will find your logo, my photo and design guidelines for a new business card. The final design will need two separate files to create an embossed card. The cards will be printed by www.plinkprint.com (Instructions below)
Format is the Plink SQUARE card
Quarrybend Marble And Tile is a brick and mortar, retail stone and tile shop.
One the front:
Quarrybend Marble And Tile
Dorian Fesslock
Owner
24807 Hollis Verdant Blvd
Suite P & R
Charlotte, NC 28193
Cell: 704-583-7142
Web: www.QuarrybendMarbleAndTile.com
(Make each word of the domain a different or alternating color)
On the back;
Something that shows beautiful colorful tile
Follow the design guide closely please. For more information see this page that describes creating the spot gloss file: https://www.plinkprint.com/us/business-cards/design-guidelines-spot-gloss
The logo is what we would like to have raised spot glossed.
Format is the Plink SQUARE card. See attahced guidlines.

```html
<!DOCTYPE html>
<html lang="en">
<head>
<meta charset="utf-8">
<title>Quarrybend Marble &amp; Tile – Square Business Card</title>
<link href="https://fonts.googleapis.com/css2?family=Montserrat:wght@300;400&family=Tinos:wght@400;700&display=swap" rel="stylesheet">
<style>
  :root {
    --bg: #c3c4c6;
    --card: #030303;
    --gold: #d0902f;
    --rust: #c0552d;
    --slate: #2d4250;
    --slate-soft: #3a5160;
    --sage: #7e8a70;
    --white: #ffffff;
  }
  * { margin: 0; padding: 0; box-sizing: border-box; }
  html, body { width: 1200px; height: 900px; overflow: hidden; background: var(--bg); }
  .canvas { position: relative; width: 1200px; height: 900px; }

  .card {
    position: absolute;
    width: 470px;
    height: 472px;
    background: var(--card);
    overflow: hidden;
  }
  .card-front { left: 107px; top: 215px; }
  .card-back  { left: 616px; top: 214px; }
  .card-band {
    position: absolute; left: 0; right: 0; bottom: 0; height: 18px;
    background: var(--gold);
  }

  /* Front – brand lockup */
  .brand-mark {
    position: absolute; left: 66px; top: 92px; width: 70px; height: 70px;
    background: var(--slate);
  }
  .brand-name {
    position: absolute; left: 180px; top: 90px; width: 260px;
    font-family: "Tinos", serif; font-weight: 400;
    color: var(--slate-soft);
    text-transform: uppercase;
  }
  .brand-name .brand-main { display: block; font-size: 31px; letter-spacing: 0.06em; line-height: 1; }
  .brand-name .brand-sub  { display: block; font-size: 14px; letter-spacing: 0.42em; margin-top: 16px; }

  /* Front – person */
  .person-name {
    position: absolute; left: 33px; top: 256px;
    font-family: "Tinos", serif; font-weight: 700; font-size: 25px;
    color: var(--white);
  }
  .person-title {
    position: absolute; left: 33px; top: 286px;
    font-family: "Montserrat", sans-serif; font-weight: 300; font-size: 14px;
    color: var(--gold);
  }
  .person-rule {
    position: absolute; left: 33px; top: 307px; width: 392px; height: 1px;
    background: var(--gold);
  }
  .address {
    position: absolute; left: 37px; top: 321px;
    font-family: "Montserrat", sans-serif; font-weight: 400; font-size: 14px;
    line-height: 18px; color: var(--white); font-style: normal;
  }
  .contact-line {
    position: absolute; left: 37px;
    display: flex; align-items: center; gap: 8px;
    font-family: "Tinos", serif; font-size: 16px; color: var(--white);
  }
  .contact-phone { top: 386px; }
  .contact-web   { top: 411px; font-size: 15.5px; }
  .contact-line svg { width: 15px; height: 15px; flex: none; }
  .web-word-a { color: var(--gold); }
  .web-word-b { color: var(--sage); }
  .web-word-c { color: var(--rust); }

  .portrait-frame {
    position: absolute; left: 311px; top: 324px; width: 105px; height: 105px;
    border: 2px solid var(--gold); padding: 6px;
  }
  .portrait {
    width: 100%; height: 100%;
    background: linear-gradient(180deg, #2a2624 0%, #5a4538 55%, #1f2a3a 100%);
  }

  /* Back */
  .tile-pattern {
    position: absolute; inset: 0;
    background: radial-gradient(circle at 50% 45%, #1a1714 0%, #0d0c0b 60%, #060606 100%);
  }
  .back-mark {
    position: absolute; left: 201px; top: 130px; width: 70px; height: 70px;
    background: var(--gold);
  }
  .back-name {
    position: absolute; left: 0; right: 0; top: 262px;
    text-align: center;
    font-family: "Tinos", serif; font-weight: 400; color: var(--white);
    text-transform: uppercase;
  }
  .back-name .brand-main { display: block; font-size: 42px; letter-spacing: 0.07em; line-height: 1; }
  .back-name .brand-sub  { display: block; font-size: 18px; letter-spacing: 0.42em; margin-top: 20px; padding-left: 0.42em; }
</style>
</head>
<body>
<main class="canvas">

  <section class="card card-front" aria-label="Business card front">
    <div class="brand-mark" aria-hidden="true"></div>
    <h1 class="brand-name">
      <span class="brand-main">Quarrybend</span>
      <span class="brand-sub">Marble &amp; Tile</span>
    </h1>

    <h2 class="person-name">Dorian Fesslock</h2>
    <p class="person-title">Owner</p>
    <div class="person-rule"></div>

    <address class="address">
      24807 Hollis Verdant Blvd<br>
      Suite P &amp; R<br>
      Charlotte, NC 28193
    </address>

    <p class="contact-line contact-phone">
      <svg viewBox="0 0 16 16" aria-hidden="true">
        <path d="M1 5c0-2 3-3 7-3s7 1 7 3v1h-4V5H5v1H1z" fill="#d0902f"/>
        <rect x="3" y="7" width="10" height="7" rx="1" fill="#d0902f"/>
      </svg>
      704-583-7142
    </p>
    <p class="contact-line contact-web">
      <svg viewBox="0 0 16 16" aria-hidden="true">
        <circle cx="8" cy="8" r="7" fill="#d0902f"/>
        <path d="M3 6c2 0 3 2 5 1s1 3 3 4M9 2c0 2 2 2 4 3" stroke="#030303" stroke-width="1.3" fill="none"/>
      </svg>
      <span>www.<span class="web-word-a">Quarrybend</span><span class="web-word-b">Marble</span><span class="web-word-c">And</span>Tile.com</span>
    </p>

    <div class="portrait-frame">
      <div class="portrait" role="img" aria-label="Portrait photo of Dorian Fesslock"></div>
    </div>

    <div class="card-band"></div>
  </section>

  <section class="card card-back" aria-label="Business card back">
    <div class="tile-pattern" role="img" aria-label="Dark repeating tile pattern background"></div>
    <div class="back-mark" aria-hidden="true"></div>
    <h2 class="back-name">
      <span class="brand-main">Quarrybend</span>
      <span class="brand-sub">Marble &amp; Tile</span>
    </h2>
    <div class="card-band"></div>
  </section>

</main>
</body>
</html>
```